Purpose, Mission, and Values Poster Update

Crestline Field Laboratories, a Testing, Inspection, and Certification company in the Atlanta area, needs an updated PMV poster. Looking to update graphics and presentation, moving away from current design. Want to carry over company logo, colors (you can include additional blues in the design beyond what is mentioned in the brand guidelines as the previous design did), and messaging (see attachments).

We would also like a companion poster, using the same design language, that shows our goals for leads and won opportunities. Want to carry over logo, colors, and messaging from original, except for this one we want the leads goal to be 115 instead of 85.

Both posters need to be 6000w x 7200h at 300ppi, CMYK. We want to move away from the cartoony, corporate clipart sort of look that the current design has, as new leadership doesn't like the aesthetic.

Target Market(s)

Internal - group of engineers, chemists, scientists, and other technical personnel

Industry/Entity Type

TIC (Testing, Inspection, Certification)

Font styles to use
Serif
Sans Serif

Colors
0054AA
0677BA
7BADD7
CADEEF
E8F1F8

Requirements
Must have
• For both: CMYK colors for printing, 6000w x 7200h at 300ppi for poster sizing leads, company logo; for PMV poster: phrasing of purpose, mission, and values statements preserved; for ring the bell poster: leads goal updated to 115, opportunities goal unchanged at 25
Should not have
• Corporate clipart, cartoon characters

```html
<!DOCTYPE html>
<html lang="en">
<head>
<meta charset="utf-8">
<title>Crestline Field Laboratories — Poster Set</title>
<link href="https://fonts.googleapis.com/css2?family=Archivo:wght@800;900&family=Urbanist:wght@300;400;500;600;700;800&display=swap" rel="stylesheet">
<style>
  :root{
    --board:#2b34af;
    --navy:#0b0b1a;
    --brand-deep:#0054aa;
    --brand-mid:#0677ba;
    --brand-sky:#7badd7;
    --brand-mist:#cadeef;
    --brand-ice:#e8f1f8;
    --white:#ffffff;
    --ink:#15151f;
    --gold-a:#ffd83a;
    --gold-b:#e0a10a;
  }
  *{margin:0;padding:0;box-sizing:border-box}
  html,body{width:1200px;height:795px;overflow:hidden;background:var(--board)}
  body{position:relative;font-family:"Urbanist",sans-serif;color:var(--ink)}
  .abs{position:absolute}
  .board-label{position:absolute;top:28px;width:300px;text-align:center;color:var(--white);
    font-size:17px;font-weight:500;letter-spacing:.22em}
  .poster{position:absolute;top:63px;width:521px;height:667px;overflow:hidden;
    box-shadow:0 22px 26px -12px rgba(10,12,70,.55)}

  /* ---------- Poster 01: ring the bell ---------- */
  .bell-poster{left:71px;
    background:linear-gradient(180deg,var(--brand-sky) 0%,var(--brand-mist) 32%,var(--brand-ice) 55%,var(--brand-mist) 78%,var(--brand-sky) 100%)}
  .brand{position:absolute;left:0;right:0;text-align:center;font-weight:700;font-size:15px;
    display:flex;align-items:center;justify-content:center;gap:7px}
  .brand .mark{width:11px;height:11px;display:inline-block}
  .bell-poster .brand{top:70px;color:var(--navy)}
  .bell-poster .brand .mark{background:var(--navy)}
  .kicker{top:120px;left:0;right:0;text-align:center;font-size:17px;font-weight:400;color:var(--ink)}
  .tagline{top:146px;left:0;right:0;text-align:center;font-size:25px;font-weight:600;color:var(--ink);letter-spacing:-.01em}
  .headline{font-family:"Archivo",sans-serif;font-weight:900;letter-spacing:-.05em;line-height:1;
    transform:scaleX(.84);transform-origin:left top;white-space:nowrap}
  .hl-we{left:121px;top:198px;font-size:54px;color:var(--navy)}
  .hl-ring{left:221px;top:178px;font-size:76px;color:var(--brand-deep)}
  .hl-the{left:113px;top:240px;font-size:76px;color:var(--navy)}
  .hl-bell{left:273px;top:258px;font-size:54px;color:var(--brand-mid)}
  .bell-art{left:137px;top:300px;width:243px;height:232px}
  .stat{position:absolute;top:553px;width:202px;height:77px;display:flex;align-items:center}
  .stat-leads{left:54px;background:var(--brand-deep)}
  .stat-won{left:265px;background:var(--white)}
  .stat .num{font-family:"Archivo",sans-serif;font-weight:800;font-size:46px;letter-spacing:-.05em;width:104px;text-align:center}
  .stat .rule{width:1px;height:52px}
  .stat .label{padding-left:9px;line-height:1.1}
  .stat .label b{display:block;font-weight:700;font-size:21px;letter-spacing:-.02em}
  .stat .label small{display:block;font-size:11px;font-weight:400}
  .stat .label span{display:block;font-size:14px;font-weight:400;margin-top:3px}
  .stat-leads .num{color:var(--brand-mist)}
  .stat-leads .rule{background:rgba(255,255,255,.45)}
  .stat-leads .label b{color:var(--brand-mist)}
  .stat-leads .label span{color:var(--white)}
  .stat-won .num{color:var(--brand-mid)}
  .stat-won .rule{background:var(--brand-mid)}
  .stat-won .label b{color:var(--brand-mid)}
  .stat-won .label small,.stat-won .label span{color:var(--ink)}

  /* ---------- Poster 02: purpose, mission, values ---------- */
  .pmv-poster{left:609px;background:linear-gradient(180deg,#f7f9fc,var(--brand-ice))}
  .purpose-panel{left:35px;top:36px;width:451px;height:286px;border-radius:0 30px 0 30px;
    background:linear-gradient(120deg,var(--brand-deep) 0%,var(--brand-mid) 55%,var(--brand-sky) 100%)}
  .purpose-pointer{left:94px;top:320px}
  .people-art{left:0;top:76px;width:70px;height:226px;border-radius:0 50px 50px 0;
    background:linear-gradient(180deg,var(--brand-sky),var(--brand-deep))}
  .city-art{left:440px;top:99px;width:81px;height:233px;
    background:linear-gradient(180deg,rgba(200,215,230,0),rgba(185,198,212,.9))}
  .target-art{left:430px;top:256px;width:64px;height:64px;border-radius:50%;
    background:radial-gradient(circle,#ffffff 0 18%,#e23030 19% 38%,#ffffff 39% 55%,#d81f26 56%)}
  .pmv-poster .brand{top:79px;color:var(--white);left:35px;right:35px}
  .pmv-poster .brand .mark{background:var(--white)}
  .pill{position:absolute;border-radius:7px;font-size:17px;font-weight:500;text-align:center;line-height:33px}
  .pill-purpose{left:198px;top:135px;width:125px;height:33px;background:var(--brand-mist);color:var(--navy)}
  .pill-mission{left:301px;top:290px;width:134px;height:31px;line-height:31px;background:var(--brand-deep);color:var(--white)}
  .purpose-1{left:35px;right:35px;top:172px;text-align:center;font-size:37px;font-weight:300;color:var(--white);letter-spacing:-.01em}
  .purpose-2{left:35px;right:35px;top:208px;text-align:center;font-size:37px;font-weight:800;color:var(--brand-mist);letter-spacing:-.01em}
  .mission-card{left:279px;top:265px;width:198px;height:166px;background:var(--white);
    border:1px solid var(--brand-sky);border-radius:30px 0 0 0}
  .mission-text{left:301px;top:327px;width:176px;font-size:17px;line-height:21px;font-weight:400;color:var(--ink)}
  .values-title{left:57px;top:351px;font-size:20px;font-weight:800;color:var(--navy);letter-spacing:-.01em}
  .value{position:absolute;width:205px}
  .value .n{position:absolute;left:-28px;top:-2px;font-size:40px;font-weight:300;line-height:1;color:var(--brand-sky)}
  .value h3{font-size:14px;font-weight:700;line-height:16px;letter-spacing:-.01em}
  .value p{font-size:11.6px;line-height:14.3px;font-weight:400;color:var(--ink)}
  .v-dark h3{color:var(--brand-deep)}
  .v-mid h3{color:var(--brand-mid)}
  .v-light h3{color:var(--brand-mid)}
  .v1{left:58px;top:385px}
  .v2{left:58px;top:441px}
  .v3{left:58px;top:497px}
  .v4{left:301px;top:463px;width:200px}
  .v5{left:301px;top:533px;width:200px}
  .team-art{left:65px;top:555px;width:142px;height:112px;border-radius:71px 71px 0 0;
    background:linear-gradient(180deg,var(--brand-sky),var(--brand-deep))}
</style>
</head>
<body>
  <div class="board-label" style="left:165px">POSTER 01</div>
  <div class="board-label" style="left:736px">POSTER 02</div>

  <!-- Ring the bell poster -->
  <section class="poster bell-poster">
    <div class="brand"><span class="mark"></span>Crestline Field Laboratories</div>
    <p class="abs kicker">Celebrating Our Opportunities to</p>
    <h2 class="abs tagline">Create a Safe &amp; Reliable World</h2>
    <span class="abs headline hl-we">WE</span>
    <span class="abs headline hl-ring">RING</span>
    <span class="abs headline hl-the">THE</span>
    <span class="abs headline hl-bell">BELL</span>
    <div class="abs bell-art" role="img" aria-label="Glossy golden bell ringing with sound waves"
      style="border-radius:45% 45% 30% 30%;background:radial-gradient(ellipse at 50% 45%,var(--gold-a) 0 35%,var(--gold-b) 60%,rgba(224,161,10,0) 72%)"></div>
    <div class="stat stat-leads">
      <span class="num">115</span><span class="rule"></span>
      <div class="label"><b>LEADS</b><span>Rings Once</span></div>
    </div>
    <div class="stat stat-won">
      <span class="num">25</span><span class="rule"></span>
      <div class="label"><b>WON</b><small>Opportunities</small><span>Rings Twice</span></div>
    </div>
  </section>

  <!-- Purpose, mission and values poster -->
  <section class="poster pmv-poster">
    <div class="abs purpose-panel"></div>
    <svg class="abs purpose-pointer" width="32" height="16" viewBox="0 0 32 16"><path d="M0 0H32L16 16Z" fill="#0064b2"/></svg>
    <div class="abs people-art" role="img" aria-label="Team members climbing toward a goal"></div>
    <div class="abs city-art" role="img" aria-label="City skyline of towers"></div>
    <div class="brand"><span class="mark"></span>Crestline Field Laboratories</div>
    <div class="pill pill-purpose">OUR PURPOSE</div>
    <h2 class="abs purpose-1">CREATE A SAFE</h2>
    <h2 class="abs purpose-2">&amp; RELIABLE WORLD</h2>
    <div class="abs mission-card"></div>
    <div class="abs target-art" role="img" aria-label="Target with an arrow in the bullseye"></div>
    <div class="pill pill-mission">OUR MISSION</div>
    <p class="abs mission-text">Deliver assurance through precise technical and professional services</p>

    <h2 class="abs values-title">OUR VALUES</h2>
    <div class="value v1 v-dark"><span class="n">1.</span><h3>Keep People First</h3><p>Foster a collaborative and inclusive environment for team members growth</p></div>
    <div class="value v2 v-dark"><span class="n">2.</span><h3>Deliver Service Excellence</h3><p>Provide best-in-class experiences for our clients</p></div>
    <div class="value v3 v-mid"><span class="n">3.</span><h3>Think Global, Act Local</h3><p>Utilize our combined expertise and knowledge to deliver when and where</p></div>
    <div class="value v4 v-light"><span class="n">4.</span><h3>Create Value</h3><p>Work efficiently and effectively to deliver quality results in complex environments.</p></div>
    <div class="value v5 v-light"><span class="n">5.</span><h3>Do What's Right</h3><p>Hold ourselves accountable to the highest safety, professional and personal standards</p></div>
    <div class="abs team-art" role="img" aria-label="Two professionals working beside a large target dial"></div>
  </section>
</body>
</html>
```